Falkrin homes and renovations business card design.

Would like some new card designs utilizing my new logo that look professional. I am open to different colors on the logo or utilize the same ones we have. I like the original concept but would like to see some fresh ideas and build on what we have already done.

Target Market(s)

Custom home building industry, Real estate sales, Renovation projects.

Industry/Entity Type

Home Builder

Contact Information for Business Card

Falkrin Homes and Renovations
2871 96th Avenue
Brackenford, Norvale
T2R3W8
Home : 403- 718-4063 Cell: 403- 294-5170

My info is : Dax Falkrin, President and CEO
email: falkrinhomes@maildrop-example.net
Website: falkrinhomes-example.com
websit

Requirements
Must have
• Must Use my new logo design. I am open to different colors on the logo or utilize the same ones in the existing design. I can upload the original logo design if needed.

```html
<!DOCTYPE html>
<html lang="en">
<head>
<meta charset="utf-8">
<title>Falkrin Homes and Renovations – Business Card</title>
<link rel="stylesheet" href="https://fonts.googleapis.com/css2?family=Exo+2:wght@600;700&family=Open+Sans:wght@400;600&display=swap">
<style>
  :root {
    --bg: #1c1c1c;
    --card-white: #ffffff;
    --card-shade: #ececec;
    --ink: #4a4a4a;
    --ink-soft: #5c5c5c;
    --rule: #8a8a8a;
    --gold: #b5842e;
    --gold-deep: #8f6a1f;
    --gold-bright: #f0bb2d;
    --gold-light: #d9a63a;
    --silver: #cfcfcf;
  }
  * { box-sizing: border-box; margin: 0; padding: 0; }
  html, body { width: 1200px; height: 1000px; overflow: hidden; }
  body {
    background: var(--bg);
    font-family: "Open Sans", Arial, sans-serif;
    position: relative;
  }
  .card {
    position: absolute;
    left: 280px;
    width: 640px;
    height: 366px;
    border-radius: 18px;
    overflow: hidden;
  }
  .card--front {
    top: 100px;
    background: linear-gradient(160deg, var(--card-shade) 0%, var(--card-white) 40%, var(--card-white) 100%);
  }
  .card--back {
    top: 534px;
    background: linear-gradient(125deg, var(--gold-light) 0%, var(--gold-bright) 35%, var(--gold) 75%, var(--gold-deep) 100%);
  }
  .holder { position: absolute; left: 44px; top: 52px; }
  .holder__name {
    font-family: "Exo 2", Arial, sans-serif;
    font-weight: 700;
    font-size: 31px;
    letter-spacing: 1px;
    color: var(--ink);
    line-height: 1;
  }
  .holder__title {
    font-size: 15px;
    color: var(--gold);
    margin-top: 4px;
  }
  .card__rule {
    position: absolute;
    left: 44px;
    top: 116px;
    width: 470px;
    height: 1.5px;
    background: var(--rule);
  }
  .contact {
    position: absolute;
    left: 44px;
    top: 130px;
    list-style: none;
    font-size: 14px;
    color: var(--ink-soft);
    line-height: 22px;
  }
  .contact li { display: flex; align-items: center; }
  .contact svg { width: 12px; height: 12px; margin-right: 12px; flex: none; }
  .brand {
    position: absolute;
    right: 44px;
    top: 150px;
    text-align: left;
    font-family: "Exo 2", Arial, sans-serif;
    font-weight: 600;
    color: var(--gold);
    display: flex;
    align-items: flex-start;
    gap: 8px;
  }
  .brand__mark { width: 10px; height: 10px; background: var(--gold); margin-top: 8px; }
  .brand__name { font-size: 38px; line-height: 1; letter-spacing: 1px; }
  .brand__line { font-size: 11.5px; letter-spacing: 0.4px; margin-top: 2px; }
  .address {
    position: absolute;
    right: 44px;
    top: 252px;
    text-align: right;
    font-size: 14px;
    line-height: 20px;
    color: var(--ink-soft);
    font-style: normal;
  }
  .band { position: absolute; left: 0; bottom: 0; width: 640px; height: 70px; }
  .band__url {
    position: absolute;
    left: 300px;
    bottom: 14px;
    font-size: 14.5px;
    color: var(--card-white);
    letter-spacing: 0.3px;
  }
  .brand--back {
    position: absolute;
    left: 50%;
    top: 50%;
    transform: translate(-50%, -50%);
    color: var(--silver);
    font-family: "Exo 2", Arial, sans-serif;
    font-weight: 600;
    display: flex;
    gap: 10px;
    align-items: flex-start;
  }
  .brand--back .brand__mark { background: var(--silver); width: 12px; height: 12px; margin-top: 10px; }
  .brand--back .brand__name { font-size: 52px; line-height: 1; letter-spacing: 1.5px; }
  .brand--back .brand__line { font-size: 15.5px; letter-spacing: 0.5px; margin-top: 3px; }
</style>
</head>
<body>

<section class="card card--front" aria-label="Business card front">
  <div class="holder">
    <h1 class="holder__name">DAX FALKRIN</h1>
    <p class="holder__title">President and CEO</p>
  </div>
  <div class="card__rule"></div>
  <ul class="contact">
    <li>
      <svg viewBox="0 0 12 12" aria-hidden="true"><path d="M2.5 1 L4.5 1 L5 3.5 L3.8 4.4 C4.5 6 6 7.5 7.6 8.2 L8.5 7 L11 7.5 L11 9.5 C11 10.3 10.3 11 9.5 11 C5 11 1 7 1 2.5 C1 1.7 1.7 1 2.5 1 Z" fill="var(--gold)"/></svg>
      403 718 4063
    </li>
    <li>
      <svg viewBox="0 0 12 12" aria-hidden="true"><rect x="2.5" y="0.8" width="7" height="10.4" rx="1.2" fill="none" stroke="var(--gold)" stroke-width="1.2"/></svg>
      403 294 5170
    </li>
    <li>
      <svg viewBox="0 0 12 12" aria-hidden="true"><rect x="0.8" y="2.3" width="10.4" height="7.4" fill="var(--gold)"/><path d="M1 2.6 L6 6.6 L11 2.6" fill="none" stroke="#fff" stroke-width="1"/></svg>
      falkrinhomes@maildrop-example.net
    </li>
  </ul>

  <div class="brand">
    <span class="brand__mark"></span>
    <div>
      <div class="brand__name">FALKRIN</div>
      <div class="brand__line">HOMES AND RENOVATIONS</div>
    </div>
  </div>

  <address class="address">
    2871 96th Avenue<br>Brackenford, Norvale
  </address>

  <svg class="band" viewBox="0 0 640 70" preserveAspectRatio="none" aria-hidden="true">
    <path d="M0 40 L260 40 L260 70 L0 70 Z" fill="var(--gold-bright)"/>
    <path d="M0 48 L640 48 L640 70 L0 70 Z" fill="var(--gold)"/>
    <path d="M240 70 L262 30 C266 23 270 20 280 20 L640 20 L640 70 Z" fill="var(--gold)"/>
  </svg>
  <span class="band__url">www.falkrinhomes-example.com</span>
</section>

<section class="card card--back" aria-label="Business card back">
  <div class="brand brand--back">
    <span class="brand__mark"></span>
    <div>
      <div class="brand__name">FALKRIN</div>
      <div class="brand__line">HOMES AND RENOVATIONS</div>
    </div>
  </div>
</section>

</body>
</html>
```